Copper Ridge Inquiries Letterhead

I would like to design a letterhead for a private investigation company. Our primary clients will be law firms. The business card is included below

```html
<!DOCTYPE html>
<html lang="en">
<head>
<meta charset="utf-8">
<title>Copper Ridge Inquiries Letterhead</title>
<link rel="stylesheet" href="https://fonts.googleapis.com/css2?family=Montserrat:wght@500;700&family=Roboto+Condensed:wght@400&display=swap">
<style>
  :root {
    --navy: #16355f;
    --orange: #f15f31;
    --white: #ffffff;
    --ground: #dcdcdc;
    --watermark: #e9ebf1;
  }
  * { margin: 0; padding: 0; box-sizing: border-box; }
  html, body { width: 1200px; height: 686px; overflow: hidden; background: var(--ground); }
  .canvas { position: relative; width: 1200px; height: 686px; }
  .letterhead {
    position: absolute; left: 350px; top: 19px; width: 500px; height: 648px;
    background: var(--white); overflow: hidden;
    box-shadow: 0 6px 18px rgba(0,0,0,0.18);
  }
  .letterhead__header, .letterhead__footer { position: absolute; left: 0; width: 500px; display: block; }
  .letterhead__header { top: 0; height: 170px; }
  .letterhead__footer { bottom: 0; height: 64px; }
  .brand {
    position: absolute; left: 34px; top: 34px; display: flex; align-items: center; gap: 8px;
    font-family: "Montserrat", sans-serif; font-weight: 700; font-size: 15px;
    color: var(--white); letter-spacing: 0.3px;
  }
  .brand__dot { width: 12px; height: 12px; border-radius: 50%; background: var(--orange); }
  .contact {
    position: absolute; right: 14px; top: 58px; list-style: none;
    font-family: "Montserrat", sans-serif; font-weight: 500; font-size: 10.5px;
    color: var(--white); text-align: right; line-height: 18px;
  }
  .contact__item { display: flex; justify-content: flex-end; align-items: center; gap: 6px; }
  .contact__icon { width: 10px; height: 10px; flex: none; }
  .watermark {
    position: absolute; left: 0; right: 0; top: 290px; text-align: center;
    font-family: "Montserrat", sans-serif; font-weight: 700; font-size: 40px;
    color: var(--watermark); letter-spacing: 1px;
  }
  .tagline {
    position: absolute; left: 72px; bottom: 21px; width: 250px; text-align: center;
    font-family: "Roboto Condensed", sans-serif; font-size: 12px; letter-spacing: 0.6px;
    color: var(--white);
  }
</style>
</head>
<body>
<div class="canvas">
  <section class="letterhead">
    <svg class="letterhead__header" viewBox="0 0 500 170" aria-hidden="true">
      <polygon fill="var(--navy)" points="0,0 400,0 340,105 0,105"/>
      <polygon fill="var(--orange)" points="400,0 500,0 500,165 215,165 262,105 340,105"/>
    </svg>

    <div class="brand"><span class="brand__dot"></span>Copper Ridge Inquiries</div>

    <ul class="contact">
      <li class="contact__item">210.555.0142
        <svg class="contact__icon" viewBox="0 0 10 10"><path fill="#fff" d="M2 1l2 2-1 1.2c.6 1.2 1.6 2.2 2.8 2.8L7 6l2 2-1.3 1.3C4.8 9 1 5.2.7 2.3z"/></svg></li>
      <li class="contact__item">Riverbend, TX
        <svg class="contact__icon" viewBox="0 0 10 10"><path fill="#fff" d="M5 0a3.4 3.4 0 0 1 3.4 3.4C8.4 6 5 10 5 10S1.6 6 1.6 3.4A3.4 3.4 0 0 1 5 0z"/><circle cx="5" cy="3.4" r="1.3" fill="var(--orange)"/></svg></li>
      <li class="contact__item">License NO. 04729315
        <svg class="contact__icon" viewBox="0 0 10 10"><rect x="0.5" y="1.5" width="9" height="7" rx="1" fill="#fff"/><rect x="2" y="3.5" width="3" height="1" fill="var(--orange)"/><rect x="2" y="5.5" width="5" height="1" fill="var(--orange)"/></svg></li>
      <li class="contact__item">www.copperridgeinquiries.com
        <svg class="contact__icon" viewBox="0 0 10 10"><circle cx="5" cy="5" r="4.3" fill="none" stroke="#fff" stroke-width="1.1"/><path d="M.7 5h8.6M5 .7c-2.4 2.6-2.4 6 0 8.6M5 .7c2.4 2.6 2.4 6 0 8.6" fill="none" stroke="#fff" stroke-width=".9"/></svg></li>
      <li class="contact__item">marcus@copperridgeinquiries.com
        <svg class="contact__icon" viewBox="0 0 10 10"><rect x=".5" y="2" width="9" height="6.5" fill="#fff"/><path d="M.8 2.4L5 5.6l4.2-3.2" fill="none" stroke="var(--orange)" stroke-width=".9"/></svg></li>
    </ul>

    <div class="watermark">Copper Ridge Inquiries</div>

    <svg class="letterhead__footer" viewBox="0 0 500 64" aria-hidden="true">
      <rect x="0" y="14" width="500" height="50" fill="var(--orange)"/>
      <polygon fill="var(--navy)" points="8,64 20,14 34,14 22,64"/>
      <polygon fill="var(--navy)" points="62,64 74,14 340,14 328,64"/>
      <polyline fill="none" stroke="var(--white)" stroke-width="2" points="48,14 40,44 62,44"/>
      <polyline fill="none" stroke="var(--white)" stroke-width="2" points="346,30 356,30 348,60"/>
      <polygon fill="var(--navy)" points="368,64 380,14 500,14 500,64"/>
      <polygon fill="var(--orange)" points="410,64 418,30 500,30 500,38 424,38 418,64"/>
    </svg>
    <div class="tagline">OVER 20 YEARS OF INVESTIGATIVE EXPERIENCE</div>
  </section>
</div>
</body>
</html>
```